Corvel Creamery Works ( Australian Dairy site )

We need a new website we are a new company in Australia manufacturing dairy products ( Packing Butter ) We want to have a new modern punchy website with the basic details of the company and company certifications should be linked in a pdf etc.. maybe photos of the site modernised graphics etc.. we need to show our customers our brand clean and green image of Australian high quality products packed under strict Australian quality standards.

Target Market(s)

export - Asia

Industry/Entity Type

It Company

Number of Pages Required

5+ page

Requirements
Must have
• Home page
• About us page
• Products page
• Contact us page
• Facility / Accreditations ( Under facility pdf files eg Licenses, halal etc.. )

```html
<!DOCTYPE html>
<html lang="en">
<head>
<meta charset="utf-8">
<title>Our Products – Corvel Creamery Works</title>
<link href="https://fonts.googleapis.com/css2?family=Lato:wght@400;700&family=Pacifico&display=swap" rel="stylesheet">
<style>
:root{
  --sky-top:#9fd0f8;
  --sky-bottom:#4fa4ee;
  --green:#3aa33a;
  --green-dark:#2f8f2f;
  --blue:#5aaaf2;
  --orange:#f7a81b;
  --brown:#5b4a3d;
  --brown-dark:#4d3e33;
  --white:#ffffff;
  --mint:#baf59a;
  --pale-blue:#d3e9ff;
  --footer-text:#e9e2da;
}
*{box-sizing:border-box;margin:0;padding:0}
html,body{width:742px;height:1200px;overflow:hidden;background:var(--white)}
body{font-family:"Lato",sans-serif;color:var(--white)}
.canvas{position:relative;width:742px;height:1200px;overflow:hidden}
.backdrop{position:absolute;left:0;top:0}
.brand{position:absolute;left:84px;top:30px;display:flex;align-items:center;gap:8px}
.brand-dot{width:14px;height:14px;border-radius:50%;background:var(--green)}
.brand-name{font-weight:700;font-size:15px;color:var(--green-dark);line-height:1.05;width:110px}
.main-nav{position:absolute;top:41px;left:311px;display:flex;gap:0}
.main-nav a{font-size:7px;font-weight:700;color:var(--white);text-decoration:none;letter-spacing:.2px;position:absolute;white-space:nowrap}
.main-nav a.active{color:var(--green-dark)}
.page-title{position:absolute;top:112px;left:0;width:742px;text-align:center;font-family:"Pacifico",cursive;font-size:38px;font-weight:400;color:var(--white);text-shadow:0 2px 4px rgba(0,0,0,.25)}
.intro{position:absolute;left:393px;top:284px;width:270px}
.intro .kicker{font-size:12px;margin-bottom:2px}
.intro h2{font-family:"Pacifico",cursive;font-weight:400;font-size:22px;margin-bottom:14px}
.intro .lead{font-size:8.4px;line-height:1.45;color:var(--mint);margin-bottom:12px}
.intro .note{font-size:6.8px;line-height:1.75}
.product{position:absolute;left:78px;width:278px;text-align:center}
.product h3{font-size:17px;font-weight:700;margin-bottom:10px}
.product p{font-size:7.4px;line-height:1.6;margin-bottom:18px}
.product .sizes{font-size:12px;font-weight:700}
.salted{top:585px}
.salted p{color:var(--pale-blue)}
.unsalted{top:803px}
.unsalted p{color:var(--mint)}
.footer-col{position:absolute;top:1030px;color:var(--footer-text)}
.footer-col h4{font-size:15px;font-weight:700;color:var(--white);margin-bottom:10px}
.links{left:80px}
.links li{list-style:none;font-size:7px;line-height:12px}
.contact{left:204px;width:130px}
.contact .row{display:flex;gap:5px;font-size:7px;line-height:12px;margin-bottom:0}
.contact .row.gap{margin-top:6px}
.contact svg{flex:none;margin-top:3px}
.newsletter{left:351px;width:125px}
.newsletter p{font-size:6.5px;margin-bottom:10px}
.newsletter .email{width:121px;height:22px;background:var(--brown-dark);border:1px solid #6a584a;font-size:6.5px;padding:7px 6px;color:var(--footer-text)}
.newsletter .subscribe{display:inline-block;margin-top:11px;background:var(--green);color:var(--white);font-size:6.5px;padding:4px 7px}
.footer-brand{position:absolute;left:500px;top:1046px;display:flex;align-items:center;gap:8px}
.footer-brand .brand-name{color:#9c8f85;width:120px}
.footer-brand .brand-dot{background:#9c8f85;width:34px;height:34px}
.social{position:absolute;left:578px;top:1092px;display:flex;gap:4px}
.social span{width:26px;height:26px;border-radius:50%;background:var(--green)}
.copyright{position:absolute;top:1167px;left:0;width:742px;text-align:center;font-size:7px;color:var(--footer-text)}
</style>
</head>
<body>
<div class="canvas">
  <svg class="backdrop" width="742" height="1200" viewBox="0 0 742 1200">
    <defs>
      <linearGradient id="sky" x1="0" y1="0" x2="0" y2="1">
        <stop offset="0" stop-color="var(--sky-top)"/>
        <stop offset="1" stop-color="var(--sky-bottom)"/>
      </linearGradient>
      <radialGradient id="butterPhoto" cx=".35" cy=".4" r=".7">
        <stop offset="0" stop-color="#6a6a4a"/>
        <stop offset="1" stop-color="#24261f"/>
      </radialGradient>
      <linearGradient id="dairyPhoto" x1="0" y1="0" x2="0" y2="1">
        <stop offset="0" stop-color="#e6e8ea"/>
        <stop offset=".55" stop-color="#c9b9ae"/>
        <stop offset="1" stop-color="#5f6a74"/>
      </linearGradient>
      <linearGradient id="fieldPhoto" x1="0" y1="0" x2="0" y2="1">
        <stop offset="0" stop-color="#c9d8e2"/>
        <stop offset=".2" stop-color="#6e9a4a"/>
        <stop offset=".7" stop-color="#4f7d34"/>
        <stop offset="1" stop-color="#9a5c34"/>
      </linearGradient>
    </defs>
    <rect class="sky" width="742" height="240" fill="url(#sky)"/>
    <g role="img" aria-label="Photo of a block of butter melting in a dark pan">
      <rect x="0" y="190" width="366" height="350" fill="url(#butterPhoto)"/>
    </g>
    <rect class="intro-panel" x="365" y="190" width="377" height="350" fill="var(--green)"/>
    <path d="M0,193 Q371,236 742,185 L742,170 L0,170 Z" fill="url(#sky)"/>
    <path d="M0,193 Q371,236 742,185 L742,192 Q371,246 0,202 Z" fill="var(--orange)"/>
    <path d="M0,189 Q371,226 742,181 L742,187 Q371,234 0,196 Z" fill="var(--white)"/>
    <g role="img" aria-label="Photo of packed salted butter with cheese, yoghurt and a jug of milk">
      <path d="M365,536 Q560,515 742,504 L742,768 L365,768 Z" fill="url(#dairyPhoto)"/>
    </g>
    <path d="M0,504 Q190,522 366,536 L366,768 L0,768 Z" fill="var(--blue)"/>
    <g role="img" aria-label="Photo of packed unsalted butter on a wooden table with cows grazing in a green field">
      <rect x="365" y="767" width="377" height="230" fill="url(#fieldPhoto)"/>
    </g>
    <path d="M0,732 Q190,750 366,767 L366,1000 L0,1000 Z" fill="var(--green)"/>
    <path d="M0,952 Q371,1003 742,950 L742,1200 L0,1200 Z" fill="var(--white)"/>
    <path d="M0,958 Q371,1012 742,956 L742,1200 L0,1200 Z" fill="var(--orange)"/>
    <path d="M0,968 Q371,1014 742,966 L742,1200 L0,1200 Z" fill="var(--white)"/>
    <path d="M0,972 Q371,1018 742,970 L742,1200 L0,1200 Z" fill="var(--brown)"/>
  </svg>

  <header>
    <div class="brand"><span class="brand-dot"></span><span class="brand-name">Corvel Creamery Works</span></div>
    <nav class="main-nav">
      <a style="left:0">HOME</a>
      <a style="left:47px">ABOUT US</a>
      <a class="active" style="left:106px">PRODUCTS</a>
      <a style="left:167px">FACILITY</a>
      <a style="left:221px">ACCREDITATIONS</a>
      <a style="left:304px">CONTACT US</a>
    </nav>
    <h1 class="page-title">Our Products</h1>
  </header>

  <section class="intro">
    <p class="kicker">From our family to yours</p>
    <h2>Pure Australian Butter</h2>
    <p class="lead">Corvel Creamery Works has a state of the art, fully accredited production facility in Riverton West, Victoria. We have the latest process and technology enabling us to produce the highest quality butter pats in different pack formats.</p>
    <p class="note">Our quality management system ensures that our products are compliant to the most stringent domestic and international regulatory requirements to deliver the highest quality product.</p>
  </section>

  <section class="product salted">
    <h3>Salted Butter</h3>
    <p>The perfect companion in the kitchen, Harbourline Salted Butter provides the creamy, rich flavor that only comes from butter made with cream from grass-fed cows.</p>
    <div class="sizes">Available in&nbsp; 7g-10g, 227g, 454g, 1KG</div>
  </section>

  <section class="product unsalted">
    <h3>Unsalted Butter</h3>
    <p>The perfect companion in the kitchen, Harbourline Unsalted Butter provides the creamy, rich flavor that only comes from butter made with cream from grass-fed cows.</p>
    <div class="sizes">Available in&nbsp; 7g-10g, 227g, 454g, 1KG</div>
  </section>

  <footer>
    <div class="footer-col links">
      <h4>Quick Links</h4>
      <ul><li>Home</li><li>About us</li><li>Products</li><li>Facility</li><li>Accreditations</li><li>Contact us</li></ul>
    </div>
    <div class="footer-col contact">
      <h4>Contact Us</h4>
      <div class="row"><svg width="7" height="7" viewBox="0 0 10 10"><path d="M2,0 L4,3 L3,4 Q4,6 6,7 L7,6 L10,8 L8,10 Q2,9 0,2 Z" fill="currentColor"/></svg><span>+61 3 9000 4812</span></div>
      <div class="row"><svg width="7" height="6" viewBox="0 0 10 8"><rect x=".5" y=".5" width="9" height="7" fill="none" stroke="currentColor"/><path d="M.5,.5 L5,4.5 L9.5,.5" fill="none" stroke="currentColor"/></svg><span>info@corvelcreamery.com.au</span></div>
      <div class="row gap"><svg width="6" height="8" viewBox="0 0 8 11"><path d="M4,0 A4,4 0 0 1 8,4 Q8,6 4,11 Q0,6 0,4 A4,4 0 0 1 4,0 Z" fill="currentColor"/></svg><span>18 Fenwick Lane, Riverton West, Victoria 3099 Australia</span></div>
    </div>
    <div class="footer-col newsletter">
      <h4>Newsletter</h4>
      <p>Sign Up for Our Newsletter &amp; Promotion</p>
      <div class="email">Enter Your email Id</div>
      <span class="subscribe">SUBSCRIBE</span>
    </div>
    <div class="footer-brand"><span class="brand-dot"></span><span class="brand-name">Corvel Creamery Works</span></div>
    <div class="social"><span></span><span></span><span></span></div>
    <p class="copyright">© 2016 corvelcreamery.com.au</p>
  </footer>
</div>
</body>
</html>
```